Help our Sugar Loom find our winning design! We're looking for a business card....

We’re a Sugar Loom in NY specializing in custom-made cakes and unique desserts.
Our cakes combine flavor and art, each designed to match customer’s special event and theme.
We’d like a unique business card with a clean design that will combine French chic and artistic look & feel.
We’d like to differentiate ourselves from standard bakeries, please don’t offer cupcake images :-)
Our logo is peach-pink and brown and we’d love to use these colors ( . Another color that can be added is gold - or feel free to suggest!

Target Market(s)

Women, ages 25-55

Industry/Entity Type

Boutique

Contact Information for Business Card

Text on card:
Logo
Sugar Loom by Dana Welch

www.sugarloomsweets.com
hello@sugarloom.com
(516) 555-0147
F – sugarloomnyc
IG - sugarloom_ny

Font styles to use
Sans Serif
Script

Requirements
Must have
• Logo
• Clean look
• French chic and artistic look & feel.
Nice to have
• Damask pattern
Should not have
• Cupcake images

```html
<!DOCTYPE html>
<html lang="en">
<head>
<meta charset="utf-8">
<title>Sugar Loom – Business Card</title>
<link href="https://fonts.googleapis.com/css2?family=Great+Vibes&family=Open+Sans:wght@400;600&display=swap" rel="stylesheet">
<style>
  :root {
    --backdrop: #c8c8c8;
    --card: #2a1a1c;
    --card-edge: #3a2628;
    --peach: #e9b3a3;
    --cream: #f6ece8;
    --rule: #8a6a66;
  }
  * { box-sizing: border-box; margin: 0; padding: 0; }
  html, body {
    width: 1200px; height: 852px; overflow: hidden;
    background: var(--backdrop);
  }
  .stage { position: relative; width: 1200px; height: 852px; }

  .card {
    position: absolute;
    width: 520px; height: 300px;
    border-radius: 28px;
    background: linear-gradient(135deg, var(--card-edge) 0%, var(--card) 55%, #24161a 100%);
    box-shadow: 0 6px 18px rgba(0,0,0,.25);
    overflow: hidden;
  }
  .card--front { left: 90px; top: 120px; }
  .card--back  { left: 590px; top: 430px; }

  .brand-name {
    font-family: "Great Vibes", cursive;
    color: var(--cream);
    font-weight: 400;
    white-space: nowrap;
  }
  .card--front .brand-name {
    position: absolute; left: 0; right: 0; top: 108px;
    text-align: center; font-size: 64px; line-height: 1;
  }
  .card--back .brand-name {
    position: absolute; left: 0; width: 260px; top: 122px;
    text-align: center; font-size: 44px; line-height: 1;
  }

  .divider {
    position: absolute; left: 268px; top: 40px;
    width: 1px; height: 220px;
    background: var(--rule);
  }

  .owner {
    position: absolute; left: 296px; top: 62px;
    color: var(--cream);
  }
  .owner__label {
    font-family: "Open Sans", sans-serif;
    font-size: 14px; letter-spacing: .3px;
  }
  .owner__name {
    font-family: "Great Vibes", cursive;
    font-size: 32px; line-height: 1.1;
  }

  .contacts {
    position: absolute; left: 296px; top: 150px;
    list-style: none;
    font-family: "Open Sans", sans-serif;
    font-size: 12px; color: var(--peach);
  }
  .contacts li { display: flex; align-items: center; gap: 9px; height: 19px; }
  .contacts svg { width: 11px; height: 11px; flex: none; }
</style>
</head>
<body>
<main class="stage">

  <section class="card card--front" aria-label="Card front">
    <div class="brand-name">Sugar Loom</div>
  </section>

  <section class="card card--back" aria-label="Card back">
    <div class="brand-name">Sugar Loom</div>
    <div class="divider"></div>

    <div class="owner">
      <p class="owner__label">Sugar Loom by</p>
      <p class="owner__name">Dana Welch</p>
    </div>

    <ul class="contacts">
      <li>
        <svg viewBox="0 0 12 12" aria-hidden="true"><path fill="#e9b3a3" d="M2.5 1h2l1 2.5-1.3 1a6 6 0 0 0 3.3 3.3l1-1.3L11 7.5v2c0 .8-.7 1.5-1.5 1.5A8.5 8.5 0 0 1 1 2.5C1 1.7 1.7 1 2.5 1z"/></svg>
        (516) 555-0147
      </li>
      <li>
        <svg viewBox="0 0 12 12" aria-hidden="true"><rect x="1" y="2.5" width="10" height="7" fill="none" stroke="#e9b3a3" stroke-width="1.2"/><path d="M1 2.5l5 4 5-4" fill="none" stroke="#e9b3a3" stroke-width="1.2"/></svg>
        hello@sugarloom.com
      </li>
      <li>
        <svg viewBox="0 0 12 12" aria-hidden="true"><circle cx="6" cy="6" r="5" fill="none" stroke="#e9b3a3" stroke-width="1.1"/><ellipse cx="6" cy="6" rx="2.2" ry="5" fill="none" stroke="#e9b3a3" stroke-width="1"/><path d="M1 6h10" stroke="#e9b3a3" stroke-width="1"/></svg>
        www.sugarloomsweets.com
      </li>
      <li>
        <svg viewBox="0 0 12 12" aria-hidden="true"><rect x="1" y="1" width="10" height="10" rx="1.5" fill="#e9b3a3"/></svg>
        sugarloomnyc
      </li>
      <li>
        <svg viewBox="0 0 12 12" aria-hidden="true"><rect x="1" y="1" width="10" height="10" rx="1.5" fill="#e9b3a3"/></svg>
        sugarloom_ny
      </li>
    </ul>
  </section>

</main>
</body>
</html>
```